Business card design for holistic health care clinic

We need a double-sided business card design for our holistic health care clinic that integrates our logo design and also its color scheme. My business is called Valmira. It is an integrative medicine clinic. You have already done the logo for me. Please ensure an elegant and upscale design that is not cluttered, but still has all the necessary information (please see below for details).

Target Market(s)

Wellness, fitness, rehabilitation for educated, well-traveled open-minded clients who are focused on natural, organic, balanced and preventive healthcare and lifestyle.

Industry/Entity Type

Medical

Contact Information for Business Card

Modern, clean.

Number of Pages Required

1 page

Font styles to use
Serif
Sans Serif

Colors

Designer to choose colors to be used in the design.

Requirements
Must have
• Logo on one side, all other information on the other side.
• Other information should include:
• Tobias Wrenfeld - DOE, CPT, LMT
• 4100 East Marrow Drive
• Austin, TX 78119
• 512 555 0148
• 818 555 0192
• info@ValmiraHealth.example
• t.wrenfeld@ValmiraHealth.example
Nice to have
• Darker background on front - but not totally black - shaded/dark gray.

```html
<!DOCTYPE html>
<html lang="en">
<head>
<meta charset="utf-8">
<title>Valmira – Business Card</title>
<link rel="stylesheet" href="https://fonts.googleapis.com/css2?family=Roboto+Condensed:wght@700&family=Roboto:wght@400;500&display=swap">
<style>
  :root {
    --backdrop: #efefef;
    --card-dark: #272727;
    --card-light: #f4f4f4;
    --brand-blue: #1b8fd2;
    --text-light: #f2f2f2;
    --text-grey: #4a4a4a;
  }
  * { margin: 0; padding: 0; box-sizing: border-box; }
  html, body {
    width: 1200px; height: 960px; overflow: hidden;
    background: var(--backdrop);
  }
  .canvas { position: relative; width: 1200px; height: 960px; }
  .card {
    position: absolute; width: 600px; height: 344px;
    box-shadow: 0 3px 6px rgba(0,0,0,0.35);
  }
  .card--front { left: 314px; top: 113px; background: var(--card-dark); }
  .card--back { left: 311px; top: 472px; background: var(--card-light); }

  .side-band {
    position: absolute; left: 0; top: 0; width: 18px; height: 100%;
    background: var(--brand-blue);
  }
  .contact {
    position: absolute; left: 44px; top: 100px;
    font-family: "Roboto", sans-serif; color: var(--text-light);
    font-size: 14.5px; line-height: 19px;
  }
  .contact__name {
    font-family: "Roboto Condensed", sans-serif; font-weight: 700;
    font-size: 22px; line-height: 24px; color: var(--brand-blue);
    text-transform: uppercase;
  }
  .contact__credentials {
    font-family: "Roboto Condensed", sans-serif; font-weight: 700;
    font-size: 12.5px; line-height: 14px; color: var(--brand-blue);
    margin-bottom: 21px;
  }
  .contact__label { color: var(--brand-blue); font-weight: 500; }
  .divider {
    width: 198px; border-top: 2px dotted var(--brand-blue);
    margin: 9px 0 9px;
  }
  .brand {
    position: absolute; display: flex; align-items: center; gap: 12px;
  }
  .brand--front { left: 330px; top: 232px; }
  .brand--back { left: 0; width: 100%; justify-content: center; top: 145px; }
  .brand__dot {
    width: 14px; height: 14px; border-radius: 50%;
    background: var(--brand-blue);
  }
  .brand__name {
    font-family: "Roboto", sans-serif; font-weight: 400;
    color: var(--brand-blue); white-space: nowrap; line-height: 1;
  }
  .brand--front .brand__name { font-size: 40px; }
  .brand--back .brand__name { font-size: 52px; }
  .tagline {
    position: absolute; left: 0; width: 100%; top: 292px; text-align: center;
    font-family: "Roboto", sans-serif; font-size: 14.5px; color: var(--text-grey);
  }
</style>
</head>
<body>
<main class="canvas">
  <section class="card card--front" aria-label="Card front">
    <div class="side-band"></div>
    <div class="contact">
      <p class="contact__name">Tobias Wrenfeld</p>
      <p class="contact__credentials">DOE, CPT, LMT</p>
      <p><span class="contact__label">P:</span> 512 555 0148</p>
      <p><span class="contact__label">C:</span> 818 555 0192</p>
      <div class="divider"></div>
      <p>4100 East Marrow Drive</p>
      <p>Austin, TX 78119</p>
      <div class="divider"></div>
      <p>t.wrenfeld@ValmiraHealth.example</p>
      <p>www.ValmiraHealth.example</p>
    </div>
    <div class="brand brand--front">
      <span class="brand__dot"></span>
      <p class="brand__name">Valmira</p>
    </div>
  </section>

  <section class="card card--back" aria-label="Card back">
    <div class="brand brand--back">
      <span class="brand__dot"></span>
      <p class="brand__name">Valmira</p>
    </div>
    <p class="tagline">it’s all about you — your health, your objectives</p>
  </section>
</main>
</body>
</html>
```